German Headhunter/ HR Consultancy needs Business Cards Design

We need a business Card Design for our Company in Stuttgart. We are specialized as Headhunter/ HR Consultancy in Placement of specialist and managers in permanent employment. Please refer to our business logo.

```html
<!DOCTYPE html>
<html lang="en">
<head>
<meta charset="utf-8">
<title>Kernwerk Personalberatung – Business Cards</title>
<link href="https://fonts.googleapis.com/css2?family=Karla:wght@400;700&display=swap" rel="stylesheet">
<style>
  :root {
    --backdrop: #d9d9db;
    --card-white: #ffffff;
    --card-dark: #5c5e62;
    --brand-blue: #2e3a9e;
    --text-grey: #5a5a5e;
    --text-light: #f2f2f2;
    --mark-dark: #2a2b2e;
  }
  * { margin: 0; padding: 0; box-sizing: border-box; }
  html, body {
    width: 1200px; height: 800px; overflow: hidden;
    background: var(--backdrop);
    font-family: "Karla", Arial, sans-serif;
  }
  .canvas { position: relative; width: 1200px; height: 800px; }

  .card {
    position: absolute;
    width: 540px; height: 310px;
    border-radius: 22px;
    box-shadow: 0 10px 28px rgba(0,0,0,0.18);
  }

  /* Front */
  .card-front { left: 60px; top: 90px; background: var(--card-white); }
  .brand-front {
    position: absolute; top: 56px; right: 70px;
    display: flex; align-items: center; gap: 12px;
    color: var(--brand-blue); font-weight: 700;
  }
  .brand-square { width: 26px; height: 26px; background: var(--brand-blue); }
  .brand-name { font-size: 26px; line-height: 1; letter-spacing: 0.5px; }
  .brand-sub { font-size: 12px; letter-spacing: 2.2px; margin-top: 3px; }

  .divider {
    position: absolute; left: 36px; right: 36px; top: 178px;
    height: 1px; background: var(--brand-blue);
  }
  .person {
    position: absolute; left: 36px; top: 150px;
    color: var(--brand-blue); font-weight: 700; font-size: 20px; letter-spacing: 0.5px;
    text-transform: uppercase;
  }
  .role {
    position: absolute; left: 36px; top: 186px;
    color: var(--text-grey); font-size: 13px;
  }
  .contacts {
    position: absolute; left: 36px; top: 210px;
    list-style: none; color: var(--text-grey); font-size: 13px; line-height: 19px;
  }
  .contacts li { display: flex; align-items: center; gap: 8px; }
  .contacts svg { width: 11px; height: 11px; fill: var(--brand-blue); }

  .address {
    position: absolute; right: 36px; top: 100px;
    text-align: right; color: var(--text-grey); font-size: 13px; line-height: 18px;
  }
  .address .web { color: var(--brand-blue); }

  /* Back */
  .card-back { left: 600px; top: 400px; background: var(--card-dark); }
  .brand-back {
    position: absolute; top: 92px; left: 0; right: 0;
    display: flex; justify-content: center; align-items: center; gap: 16px;
    color: var(--mark-dark); font-weight: 700;
  }
  .brand-back .brand-square { width: 40px; height: 40px; background: var(--mark-dark); }
  .brand-back .brand-name { font-size: 40px; }
  .brand-back .brand-sub { font-size: 17px; letter-spacing: 3px; }
  .tagline {
    position: absolute; left: 40px; right: 40px; bottom: 48px;
    text-align: center; color: var(--text-light); font-size: 14px; line-height: 20px;
  }
</style>
</head>
<body>
<main class="canvas">

  <section class="card card-front" aria-label="Business card front">
    <div class="brand-front">
      <span class="brand-square"></span>
      <div>
        <div class="brand-name">KERNWERK</div>
        <div class="brand-sub">PERSONALBERATUNG</div>
      </div>
    </div>

    <div class="address">
      Kernwerk Personalberatung<br>
      1420 Linden Court<br>
      Harbor City, Oregon 97311<br>
      <span class="web">www.kernwerk-hr.com</span>
    </div>

    <div class="person">Jonas Albrecht</div>
    <div class="divider"></div>
    <div class="role">Founder &amp; CEO</div>

    <ul class="contacts">
      <li><svg viewBox="0 0 12 12"><path d="M2 1h3l1 3-1.5 1a6 6 0 0 0 2.5 2.5L8 6l3 1v3a1 1 0 0 1-1 1A9 9 0 0 1 1 2a1 1 0 0 1 1-1z"/></svg>555-214-7360</li>
      <li><svg viewBox="0 0 12 12"><path d="M3 0h6a1 1 0 0 1 1 1v10a1 1 0 0 1-1 1H3a1 1 0 0 1-1-1V1a1 1 0 0 1 1-1zm0 2v8h6V2z"/></svg>555-382-9147</li>
      <li><svg viewBox="0 0 12 12"><path d="M1 4h10v7H1zM3 1h6v2H3z"/></svg>555-671-2085</li>
      <li><svg viewBox="0 0 12 12"><path d="M0 2h12v8H0zm1 1v.5L6 7l5-3.5V3z"/></svg>jonas@kernwerk-hr.com</li>
    </ul>
  </section>

  <section class="card card-back" aria-label="Business card back">
    <div class="brand-back">
      <span class="brand-square"></span>
      <div>
        <div class="brand-name">KERNWERK</div>
        <div class="brand-sub">PERSONALBERATUNG</div>
      </div>
    </div>
    <p class="tagline">We are specialized as Headhunter/ HR Consultancy in Placement of specialist and managers in permanent employment.</p>
  </section>

</main>
</body>
</html>
```